Homemaking training schools needs a Business Card design

Designer, Hello!

No special requirements, good-looking enough.
--------------------------------------------------------------------------

Name: Marcus Dole
Chairman
Tel: 0574-71948263
Mobile: 13857420916
Email: kelvora@mailnest.example
Web: www.prt2019.example
Add: No.258, LanpingJie, BeiyuanQu, Ningbo, Zhejiang

LOGO
Ningbo PRT Homemaking Training School

Target Market(s)

pregnant women, mothers, infants, the elderly and families, including cleaning, cooking, nursing training.

Industry/Entity Type

Business

Contact Information for Business Card

Name: Marcus Dole
Chairman
Tel: 0574-71948263
Mobile: 13857420916
Email: kelvora@mailnest.example
Web: www.prt2019.example

LOGO

Font styles to use
Serif
Sans Serif
Decorative

Requirements
Nice to have
• Feels: clean, specifications, safety, comfort, warmth and happiness.

```html
<!DOCTYPE html>
<html lang="en">
<head>
<meta charset="utf-8">
<title>PengRuiTang Business Card</title>
<link rel="stylesheet" href="https://fonts.googleapis.com/css2?family=Mulish:wght@400;600;700;800&display=swap">
<style>
  :root {
    --brand-blue: #0a76bd;
    --paper-white: #ffffff;
    --ink-dark: #1f1f1f;
    --backdrop: #eeeeec;
  }
  * { margin: 0; padding: 0; box-sizing: border-box; }
  html, body {
    width: 1200px;
    height: 1194px;
    overflow: hidden;
    background: var(--backdrop);
    font-family: "Mulish", sans-serif;
  }
  .card {
    position: absolute;
    left: 214px;
    width: 794px;
    height: 514px;
    background: var(--brand-blue);
    box-shadow: 0 6px 18px rgba(0, 0, 0, 0.18);
    overflow: hidden;
  }
  .card-front { top: 54px; }
  .card-back { top: 622px; }

  .brand-name {
    position: absolute;
    left: 0;
    width: 100%;
    top: 250px;
    text-align: center;
    color: var(--paper-white);
    font-weight: 700;
    font-size: 72px;
    line-height: 1;
    letter-spacing: -0.5px;
  }

  .band {
    position: absolute;
    left: 0;
    top: 0;
    width: 794px;
    height: 514px;
  }
  .contact {
    position: absolute;
    left: 103px;
    color: var(--paper-white);
    line-height: 1;
    white-space: nowrap;
  }
  .contact-name { top: 98px; font-size: 35px; font-weight: 800; letter-spacing: 0.3px; }
  .contact-title { top: 144px; font-size: 32px; font-weight: 400; }
  .contact-line { font-size: 25px; font-weight: 400; }
  .contact-tel { top: 181px; }
  .contact-mobile { top: 212px; }
  .contact-email { top: 243px; }
  .address {
    position: absolute;
    left: 103px;
    top: 316px;
    color: var(--ink-dark);
    font-size: 25px;
    line-height: 32px;
  }
  .website {
    position: absolute;
    left: 103px;
    top: 418px;
    color: var(--paper-white);
    font-size: 25px;
    line-height: 1;
  }
</style>
</head>
<body>
  <section class="card card-front">
    <h1 class="brand-name">PengRuiTang</h1>
  </section>

  <section class="card card-back">
    <svg class="band" viewBox="0 0 794 514" aria-hidden="true">
      <rect x="0" y="295" width="794" height="104" fill="#ffffff"/>
      <polygon points="640,296 676,262 714,296" fill="#ffffff"/>
      <polygon points="636,399 676,364 718,399" fill="#0a76bd"/>
    </svg>
    <p class="contact contact-name">MARCUS DOLE</p>
    <p class="contact contact-title">Chairman</p>
    <p class="contact contact-line contact-tel">Tel: 0574-71948263</p>
    <p class="contact contact-line contact-mobile">Mobile: 13857420916</p>
    <p class="contact contact-line contact-email">Email: kelvora@mailnest.example</p>
    <p class="address">No.258, LanpingJie, BeiyuanQu, Ningbo,<br>Zhejiang</p>
    <p class="website">www.prt2019.example</p>
  </section>
</body>
</html>
```